English and Spanish Language School Needs a Business Card

Need a business card design a startup company called Maribel Language School. The company will offer English and Spanish conversational level courses designed to make the learner feel comfortable with grammar and vocabulary. We would like to see a logo with some colour that should communicate learning, growth.

Target Market(s)

Consumers and businesses

Industry/Entity Type

Education

Contact Information for Business Card

TBD

Font styles to use
Serif

Requirements
Must have
• Include the following
• Logo
• Name
• Title
• Cellphone Number
• Office Phone number
• Email address
• Office Address

```html
<!DOCTYPE html>
<html lang="en">
<head>
<meta charset="utf-8">
<title>Maribel Language School – Business Card</title>
<link rel="stylesheet" href="https://fonts.googleapis.com/css2?family=Nunito:wght@800&family=Lora:wght@400;700&display=swap">
<style>
  :root {
    --red: #d4212f;
    --red-deep: #b81826;
    --teal: #1bb5be;
    --white: #ffffff;
    --paper: #f4f4f4;
    --stage: #e6e3de;
  }
  * { margin: 0; padding: 0; box-sizing: border-box; }
  html, body { width: 1200px; height: 780px; overflow: hidden; }
  body {
    background: var(--stage);
    position: relative;
    font-family: "Lora", Georgia, serif;
  }
  .card {
    position: absolute;
    top: 240px;
    width: 520px;
    height: 300px;
    border-radius: 18px;
    overflow: hidden;
    box-shadow: 0 8px 22px rgba(0,0,0,.18);
  }
  .card--front { left: 60px; background: var(--paper); }
  .card--back {
    left: 620px;
    background: radial-gradient(circle at 45% 40%, #dc2a36 0%, var(--red-deep) 100%);
    display: flex; align-items: center; justify-content: center;
  }
  .front-shapes { position: absolute; inset: 0; width: 100%; height: 100%; }

  .brand { font-family: "Nunito", Arial, sans-serif; font-weight: 800; line-height: 1; }
  .brand__name { display: block; letter-spacing: -1px; }
  .brand__tag { display: block; letter-spacing: .3px; }
  .card--front .brand {
    position: absolute; left: 34px; top: 112px; color: var(--red);
  }
  .card--front .brand__name { font-size: 56px; }
  .card--front .brand__tag { font-size: 17px; margin-top: 4px; padding-left: 4px; }
  .card--back .brand { color: var(--white); text-align: left; }
  .card--back .brand__name { font-size: 76px; }
  .card--back .brand__tag { font-size: 21px; margin-top: 6px; padding-left: 6px; }

  .person {
    position: absolute; top: 24px; right: 218px; text-align: right;
  }
  .person__name { color: var(--red); font-size: 16px; font-weight: 700; letter-spacing: 1px; white-space: nowrap; }
  .person__title { color: var(--teal); font-size: 13px; }

  .contact {
    position: absolute; right: 24px; top: 116px;
    color: var(--white); text-align: right; font-size: 12.5px; line-height: 1.6;
    white-space: nowrap;
  }
  .contact__row { display: flex; align-items: center; justify-content: flex-end; gap: 7px; }
  .contact__address { margin-bottom: 6px; }
  .icon { width: 13px; height: 13px; flex: none; }
</style>
</head>
<body>

<section class="card card--front" aria-label="Business card front">
  <svg class="front-shapes" viewBox="0 0 520 300" preserveAspectRatio="none" aria-hidden="true">
    <path d="M325,0 C280,90 325,210 215,300 L520,300 L520,0 Z" fill="var(--red)"/>
    <path d="M348,0 C310,90 350,210 242,300" fill="none" stroke="var(--white)" stroke-width="3" opacity=".9"/>
    <path d="M275,118 C292,205 250,262 170,300 L202,300 C270,262 298,200 275,118 Z" fill="var(--teal)"/>
  </svg>

  <div class="brand">
    <span class="brand__name">Maribel</span>
    <span class="brand__tag">Language School</span>
  </div>

  <div class="person">
    <p class="person__name">DANIEL REYES</p>
    <p class="person__title">Manager</p>
  </div>

  <div class="contact">
    <p class="contact__address">Your Address, 2nd Ste<br>Cedarvale, Texas 1234</p>
    <p class="contact__row">555 010 2030
      <svg class="icon" viewBox="0 0 14 14" aria-label="Cellphone"><rect x="1" y="1" width="12" height="12" rx="2" fill="var(--white)"/><rect x="4.5" y="3" width="5" height="8" rx="1" fill="var(--red)"/></svg>
    </p>
    <p class="contact__row">555 010 2031
      <svg class="icon" viewBox="0 0 14 14" aria-label="Office phone"><rect x="1" y="1" width="12" height="12" rx="2" fill="var(--white)"/><path d="M4,4 Q4,10 10,10 L10,8.5 L8.5,8 L7.8,8.8 Q5.2,7.5 5.2,6.2 L6,5.5 L5.5,4 Z" fill="var(--red)"/></svg>
    </p>
    <p class="contact__row">hello@maribelschool.com
      <svg class="icon" viewBox="0 0 14 14" aria-label="Email"><rect x="1" y="1" width="12" height="12" rx="2" fill="var(--white)"/><rect x="3" y="4.5" width="8" height="5.5" fill="none" stroke="var(--red)" stroke-width="1"/><path d="M3,4.5 L7,7.8 L11,4.5" fill="none" stroke="var(--red)" stroke-width="1"/></svg>
    </p>
  </div>
</section>

<section class="card card--back" aria-label="Business card back">
  <div class="brand">
    <span class="brand__name">Maribel</span>
    <span class="brand__tag">Language School</span>
  </div>
</section>

</body>
</html>
```